Buch-/E-Book-Cover für erotische Kurzgeschichten
Zielgruppe
Ich bin Autor diverser Bücher und ich benötige ein Cover für ein e-book für erotische Kurzgeschichten. Es handelt sich um Geschichten aus der Sicht einer Frau und ich denke, dass das somit vor allem Männer interessieren könnte. Zielgruppe sind also vor allem Männer, denke ich.
Aufgabenstellung
Der Name 'Lorina - Sinnliche Erzählungen mit Stil' sollte kreativ und ansprechend in das Cover einfließen.
* Wenn sinnvoll einsetzbar sollte das Foto einer Frau verwendet werden.(Ich werde es in den Dateien hinzufügen).
Wenn ein anderes Model besser zu ihrer Idee passt, nutzen sie gerne ein Stock-Bild, aber ich möchte den Kopf nach Möglichkeit nicht zeigen, und ihn der Phantasie des Lesers überlassen.
Das Foto das auf das Cover kommt, sollte eine nackte Frau mit all ihren Reizen zeigen, die aber durch etwas alltägliches wie zb.: Eine nasse Duschtüre verdeckt sein sollen. Man soll aber noch genug sehen, um den Leser neugierig zu machen. Vielleicht finden sie noch eine bessere 'verdeck Möglichkeit'.
* Wenn sie eines der beigefügte Foto nutzen, wäre es gut, wenn die Zensiert-Streifen eines der Fotos auf dem Cover nicht mehr zu sehen sind.
* Ich bringe das Buch unter dem Pseudonym 'Petra L. Mondkamm' auf den Markt. Der Name sollte ebenfall sinnvoll auf dem Cover untergebracht werden.

```html
<!DOCTYPE html>
<html lang="de">
<head>
<meta charset="utf-8">
<title>Lorina – Sinnliche Erzählungen mit Stil</title>
<link rel="stylesheet" href="https://fonts.googleapis.com/css2?family=EB+Garamond:wght@400;500&display=swap">
<style>
  :root {
    --night: #0c0f1c;
    --navy: #151b33;
    --plum: #3a2340;
    --rose: #a8627f;
    --blush: #d9a3b8;
    --ink-white: #ffffff;
    --title-red: #d40f14;
  }
  html, body {
    margin: 0;
    padding: 0;
    width: 750px;
    height: 1200px;
    overflow: hidden;
    background: var(--night);
  }
  .cover {
    position: relative;
    width: 750px;
    height: 1200px;
    overflow: hidden;
    font-family: "EB Garamond", "Times New Roman", serif;
  }
  .cover-photo {
    position: absolute;
    inset: 0;
    background:
      radial-gradient(ellipse 120px 160px at 610px 60px, rgba(217,163,184,0.55), transparent 70%),
      radial-gradient(ellipse 170px 220px at 640px 380px, rgba(200,120,150,0.55), transparent 70%),
      radial-gradient(ellipse 200px 260px at 700px 600px, rgba(168,98,127,0.5), transparent 72%),
      radial-gradient(ellipse 260px 380px at 600px 850px, rgba(90,50,85,0.55), transparent 75%),
      linear-gradient(90deg, var(--night) 0%, var(--navy) 35%, var(--plum) 60%, #4b2a45 80%, #5a2f46 100%);
  }
  .author {
    position: absolute;
    top: 518px;
    left: 0;
    width: 750px;
    text-align: center;
    font-size: 54px;
    font-weight: 400;
    letter-spacing: 0.14em;
    color: var(--ink-white);
    line-height: 1;
    padding-left: 0.14em;
    box-sizing: border-box;
  }
  .title {
    position: absolute;
    top: 578px;
    left: 0;
    width: 750px;
    text-align: center;
    font-size: 142px;
    font-weight: 500;
    color: var(--ink-white);
    line-height: 1;
    letter-spacing: -0.01em;
    text-shadow: 0 2px 2px rgba(0,0,0,0.55), 0 0 6px rgba(0,0,0,0.35);
  }
  .subtitle {
    position: absolute;
    top: 718px;
    left: 0;
    width: 750px;
    text-align: center;
    font-size: 52px;
    font-weight: 400;
    color: var(--title-red);
    line-height: 60px;
    letter-spacing: -0.03em;
    margin: 0;
  }
</style>
</head>
<body>
  <main class="cover">
    <div class="cover-photo" role="img" aria-label="Foto einer Frau hinter einer nassen, beschlagenen Duschscheibe mit Wassertropfen, in Blau-, Violett- und Rosatönen"></div>
    <p class="author" style="margin:0">Petra L. Mondkamm</p>
    <h1 class="title" style="margin:0">LORINA</h1>
    <p class="subtitle">Sinnliche Erzählungen<br>mit Stil</p>
  </main>
</body>
</html>
```